BRIGHT RIVER POWER.

I'd like my business logo.
contact name: Dennis Halvorsen
phone:0438759164
email: info@brightriverpower.net.au
website: www.brightriverpower.net.au

services:
solar
battery storage
LED lighting
energy saving solutions
general electrical
I'd like the design to look professional

Target Market(s)

Everyone

Industry/Entity Type

Business

Contact Information for Business Card

as described above

Requirements
Must have
• Id like the colours and the design to work well with my logo.

```html
<!DOCTYPE html>
<html lang="en">
<head>
<meta charset="utf-8">
<title>Bright River Power – Business Card</title>
<link rel="stylesheet" href="https://fonts.googleapis.com/css2?family=Varela+Round&display=swap">
<style>
  :root {
    --bg: #ecebe7;
    --card: #ffffff;
    --green: #2ea24a;
    --green-light: #7cc242;
    --green-text: #3a9f4a;
    --orange: #f0931e;
    --grey-text: #4f9a55;
  }
  * { box-sizing: border-box; margin: 0; padding: 0; }
  html, body {
    width: 1200px; height: 1022px; overflow: hidden;
    background: var(--bg);
    font-family: "Varela Round", sans-serif;
  }
  .card {
    position: absolute; left: 150px; top: 254px;
    width: 900px; height: 514px;
    background: var(--card);
    border-radius: 22px;
    overflow: hidden;
    box-shadow: 0 10px 30px rgba(0,0,0,0.12);
  }
  .card-bands { position: absolute; left: 0; top: 0; width: 900px; height: 514px; }
  .brand {
    position: absolute; left: 70px; top: 150px;
    display: flex; align-items: center; gap: 18px;
  }
  .brand-dot { width: 64px; height: 64px; border-radius: 50%; background: var(--green); }
  .brand-name {
    font-size: 40px; color: var(--green-text); letter-spacing: 1px; line-height: 1;
  }
  .divider {
    position: absolute; left: 120px; top: 300px; width: 705px; height: 3px;
    background: var(--green);
  }
  .holder-name {
    position: absolute; right: 75px; top: 252px;
    font-size: 32px; color: var(--orange);
  }
  .services {
    position: absolute; left: 90px; top: 322px; list-style: none;
    font-size: 21px; color: var(--green-text); line-height: 30px;
  }
  .services li { display: flex; align-items: center; gap: 16px; }
  .services li::before {
    content: ""; width: 9px; height: 9px; border-radius: 50%; background: var(--orange);
  }
  .contact {
    position: absolute; right: 50px; top: 322px; list-style: none;
    font-size: 20px; color: var(--grey-text); line-height: 32px; text-align: right;
  }
  .contact li { display: flex; align-items: center; justify-content: flex-end; gap: 18px; }
  .contact svg { width: 16px; height: 16px; flex: none; }
</style>
</head>
<body>
  <div class="card">
    <svg class="card-bands" viewBox="0 0 900 514" aria-hidden="true">
      <rect x="826" y="210" width="74" height="30" fill="var(--green)"/>
      <path d="M0 482 L560 482 L585 440 L900 440 L900 514 L0 514 Z" fill="var(--green-light)"/>
      <path d="M0 494 L570 494 L600 452 L900 452 L900 514 L0 514 Z" fill="var(--green)"/>
    </svg>

    <div class="brand">
      <span class="brand-dot"></span>
      <span class="brand-name">BRIGHT RIVER POWER</span>
    </div>

    <div class="holder-name">Dennis Halvorsen</div>
    <div class="divider"></div>

    <ul class="services">
      <li>Solar</li>
      <li>Battery storage</li>
      <li>LED lighting</li>
      <li>Energy saving solutions</li>
    </ul>

    <ul class="contact">
      <li>0438759164
        <svg viewBox="0 0 16 16"><path d="M4 1.5 L6.5 5 L5 6.5 Q6.5 9.5 9.5 11 L11 9.5 L14.5 12 L13 14.5 Q6 14 1.5 3 Z" fill="none" stroke="var(--orange)" stroke-width="1.4"/></svg>
      </li>
      <li>info@brightriverpower.net.au
        <svg viewBox="0 0 16 16"><rect x="1.5" y="3.5" width="13" height="9" fill="none" stroke="var(--orange)" stroke-width="1.4"/><path d="M1.5 3.5 L8 9 L14.5 3.5" fill="none" stroke="var(--orange)" stroke-width="1.4"/></svg>
      </li>
      <li>www.brightriverpower.net.au
        <svg viewBox="0 0 16 16"><circle cx="8" cy="8" r="6.5" fill="none" stroke="var(--orange)" stroke-width="1.4"/><ellipse cx="8" cy="8" rx="3" ry="6.5" fill="none" stroke="var(--orange)" stroke-width="1.2"/><path d="M1.5 8 H14.5" stroke="var(--orange)" stroke-width="1.2"/></svg>
      </li>
    </ul>
  </div>
</body>
</html>
```